Consulting company business cards

We have a base design, but would be willing to update. We have a new logo/"tag" that needs to be added. Current business card design is attached for reference into our "style."

Industry/Entity Type

Business

Contact Information for Business Card

Should contain name and title, office number, mobile number if appropriate, e-mail, website, physical address, and company logo.

Font styles to use
Other font styles liked:
• See current card design on KorvandBCard

Colors
0455a3
85acd3
aaaaaa

Requirements
Must have
• Our colors are navy blue, gray, and a lighter blue
Nice to have
• Design that I can easily drop in new names/titles as we hire employees.

```html
<!DOCTYPE html>
<html lang="en">
<head>
<meta charset="utf-8">
<title>Brennick business cards</title>
<link href="https://fonts.googleapis.com/css2?family=Montserrat:wght@400;500;700&display=swap" rel="stylesheet">
<style>
  :root {
    --navy: #06304d;
    --sky: #3bb0e6;
    --soft-blue: #85acd3;
    --grey: #aaaaaa;
    --ink: #1f2a33;
    --paper: #ffffff;
    --backdrop: #e9ecef;
  }
  * { box-sizing: border-box; margin: 0; padding: 0; }
  html, body { width: 1200px; height: 900px; overflow: hidden; }
  body {
    background: var(--backdrop);
    font-family: "Montserrat", sans-serif;
    position: relative;
  }
  .card {
    position: absolute;
    width: 620px;
    height: 354px;
    border-radius: 22px;
    overflow: hidden;
    box-shadow: 0 10px 28px rgba(0,0,0,0.18);
    background: var(--paper);
  }
  .card-bg { position: absolute; inset: 0; width: 100%; height: 100%; }
  .card-front { left: 140px; top: 70px; }
  .card-back { left: 440px; top: 476px; }

  .mascot-art {
    position: absolute;
    left: 238px; top: 82px;
    width: 150px; height: 150px;
    border-radius: 46% 50% 42% 48%;
    background: radial-gradient(circle at 45% 40%, #ffffff, #e4ecf3);
  }
  .front-url {
    position: absolute;
    left: 28px; bottom: 14px;
    font-size: 17px;
    font-weight: 500;
    color: var(--sky);
    letter-spacing: 0.5px;
  }
  .front-url strong, .contact-list strong { font-weight: 700; }

  .brand {
    position: absolute;
    left: 34px; top: 72px;
    display: flex; align-items: center; gap: 10px;
  }
  .brand-name {
    font-size: 40px;
    font-weight: 700;
    color: var(--navy);
    letter-spacing: 1px;
    line-height: 1;
  }
  .brand-dot {
    width: 34px; height: 34px;
    border-radius: 50%;
    background: var(--soft-blue);
  }
  .brand-tag {
    position: absolute;
    left: 36px; top: 118px;
    font-size: 11px;
    color: var(--grey);
    letter-spacing: 1.6px;
    text-transform: uppercase;
  }

  .person {
    position: absolute;
    right: 30px; top: 60px;
    text-align: right;
  }
  .person-name {
    font-size: 23px;
    font-weight: 700;
    color: var(--sky);
    letter-spacing: 1px;
    text-transform: uppercase;
  }
  .person-title {
    font-size: 14px;
    color: var(--navy);
    letter-spacing: 1px;
    text-transform: uppercase;
    padding-bottom: 6px;
    border-bottom: 1.5px solid var(--sky);
  }
  .person-address {
    margin-top: 10px;
    font-size: 14px;
    line-height: 1.35;
    color: var(--ink);
  }

  .contact-list {
    position: absolute;
    left: 104px; top: 236px;
    list-style: none;
    font-size: 14px;
    color: var(--navy);
    line-height: 1.3;
  }
  .contact-list li { display: flex; align-items: center; gap: 10px; }
  .contact-list .url { color: var(--navy); }
  .contact-list .url strong { color: var(--sky); }
  .contact-icon { width: 11px; height: 11px; flex: none; }
</style>
</head>
<body>

  <section class="card card-front" aria-label="Card front">
    <svg class="card-bg" viewBox="0 0 620 354" preserveAspectRatio="none">
      <rect width="620" height="354" fill="var(--navy)"/>
      <path d="M0 300 H255 L292 318 H620 V354 H0 Z" fill="var(--paper)"/>
      <path d="M292 318 L620 296 V312 L330 318 Z" fill="var(--sky)"/>
    </svg>
    <div class="mascot-art" role="img" aria-label="White dog head mascot illustration"></div>
    <p class="front-url">www.<strong>BRENNICKTECH</strong>.com</p>
  </section>

  <section class="card card-back" aria-label="Card back">
    <svg class="card-bg" viewBox="0 0 620 354" preserveAspectRatio="none">
      <rect width="620" height="354" fill="var(--paper)"/>
      <path d="M0 348 L436 324 L432 338 L0 356 Z" fill="var(--sky)"/>
      <path d="M445 222 H620 V354 H425 Z" fill="var(--navy)"/>
      <line x1="98" y1="228" x2="438" y2="228" stroke="var(--sky)" stroke-width="1.5"/>
    </svg>

    <div class="brand">
      <span class="brand-name">BRENNICK</span>
      <span class="brand-dot"></span>
    </div>
    <p class="brand-tag">A cloud consulting company</p>

    <div class="person">
      <p class="person-name">Renata Korvand</p>
      <p class="person-title">Office Manager</p>
      <p class="person-address">1185 w 40th st<br>fairhaven ohio 43012</p>
    </div>

    <ul class="contact-list">
      <li>
        <svg class="contact-icon" viewBox="0 0 12 12"><path d="M2 1 L4.5 1 L5.5 3.5 L4 4.8 C4.8 6.5 5.8 7.4 7.2 8 L8.5 6.5 L11 7.5 V10 C11 10.6 10.5 11 10 11 C5 11 1 7 1 2 C1 1.5 1.4 1 2 1 Z" fill="var(--sky)"/></svg>
        555.014.2910
      </li>
      <li>
        <svg class="contact-icon" viewBox="0 0 12 12"><rect x="3" y="0.5" width="6" height="11" rx="1.2" fill="var(--sky)"/><rect x="4.2" y="2" width="3.6" height="6.5" fill="#fff"/></svg>
        555.014.2971
      </li>
      <li>
        <svg class="contact-icon" viewBox="0 0 12 12"><rect x="0.8" y="2.2" width="10.4" height="7.6" rx="1" fill="none" stroke="var(--sky)" stroke-width="1.2"/><path d="M1 2.6 L6 6.6 L11 2.6" fill="none" stroke="var(--sky)" stroke-width="1.2"/></svg>
        rkorvand@brennicktech.com
      </li>
      <li class="url">
        <svg class="contact-icon" viewBox="0 0 12 12"><circle cx="6" cy="6" r="5" fill="none" stroke="var(--sky)" stroke-width="1.1"/><ellipse cx="6" cy="6" rx="2.2" ry="5" fill="none" stroke="var(--sky)" stroke-width="1"/><line x1="1" y1="6" x2="11" y2="6" stroke="var(--sky)" stroke-width="1"/></svg>
        <span>www.<strong>BRENNICKTECH</strong>.com</span>
      </li>
    </ul>
  </section>

</body>
</html>
```